Car rental website design for a UAE car rental company

This project is about creating a new website design for a car rental company located in Dubai (United Arab Emirates), I opened the same project a few months ago but I didn't receive a lot of appealing entries so I closed it but this time I am marking the project as guaranteed to avoid such situation again, if you have already provided a design before then please re-submit again on this project so that it is considered while reviewing all the designs

A few important things:

1- We need a simple non-complex design
2- The final deliverable would be 2 screens (PSD, JPEG ... etc), the first screen is for the home page and the second screen is for an internal page
3- The home page must have a section that end users can use to rent a car online directly from the home page instead of going into some inner pages
4- The current website is very old and not very appealing so avoid creating a similar design (www.crestvane-autos.example)
5- The name is Crestvane but the company rents normal cars (no Limousin cars will be rented) so avoid adding any fancy cars in the images/graphics used in the design, just normal end users cars
6- The expected pages would be: home, About us, Our team, Strategy, Contact us and links to social media pages
7- The attachments include the company's logo and some screens from other car rental companies that provide online rentals/payments

If you have any questions please feel free to ask and please note that we will need the designs urgently

Thanks

Target Market(s)

Dubai - United Arab Emirates

Industry/Entity Type

It Company

Number of Pages Required

2 page

Font styles to use
Sans Serif

Requirements
Must have
• Check the project details
Nice to have
Should not have

```html
<!DOCTYPE html>
<html lang="en">
<head>
<meta charset="utf-8">
<title>Crestvane Rent A Car</title>
<link rel="stylesheet" href="https://fonts.googleapis.com/css2?family=Arimo:ital,wght@0,400;0,700;1,700&family=Marcellus&display=swap">
<style>
:root{
  --crimson:#a50034;
  --crimson-dark:#8a002a;
  --crimson-line:#c4335f;
  --mist:#d9dedc;
  --strip:#d6d6d6;
  --ink:#222;
  --white:#fff;
  --slate:#7a7a7a;
  --charcoal:#333;
  --sky:#6f9fcc;
  --haze:#c9d8e4;
  --city:#8a8478;
}
*{margin:0;padding:0;box-sizing:border-box}
html,body{width:891px;height:1200px;overflow:hidden;background:var(--white)}
body{position:relative;font-family:"Arimo",Arial,sans-serif;color:var(--ink)}
.abs{position:absolute}

/* header */
.header{left:0;top:0;width:891px;height:140px;background:var(--crimson)}
.nav-band{left:0;top:89px;width:891px;height:49px;background:var(--crimson-dark)}
.strip{left:0;top:140px;width:891px;height:10px;background:var(--strip)}
.brand{left:124px;top:0;width:171px;height:140px;background:var(--white);text-align:center}
.brand-mark{position:absolute;left:60px;top:26px;width:51px;height:51px;border:3px solid var(--crimson)}
.brand-name{position:absolute;left:0;top:86px;width:100%;font-size:23px;color:var(--slate)}
.brand-sub{position:absolute;left:0;top:112px;width:100%;font-size:12px;letter-spacing:2px;color:var(--crimson);font-weight:700}
.car-icon{left:356px;top:16px;width:95px;height:50px;background:var(--crimson-dark);border-radius:22px 30px 10px 10px}
.slogan{font-family:"Marcellus",serif;color:var(--white)}
.slogan-main{left:467px;top:16px;font-size:26px}
.slogan-sub{left:507px;top:49px;font-size:17px}
.nav a{position:absolute;top:104px;color:var(--white);text-decoration:none;font-size:17px}
.nav-sep{top:92px;width:1px;height:44px;background:var(--crimson-line)}
.home-icon{left:379px;top:108px}

/* hero */
.hero{left:0;top:150px;width:891px;height:374px;
  background:
    radial-gradient(ellipse 230px 170px at 190px 250px, rgba(245,240,236,.75) 0%, rgba(245,240,236,0) 100%),
    radial-gradient(ellipse 150px 110px at 210px 250px, rgba(90,140,200,.45) 0%, rgba(90,140,200,0) 100%),
    radial-gradient(ellipse 120px 70px at 70px 330px, rgba(200,40,60,.55) 0%, rgba(200,40,60,0) 100%),
    radial-gradient(ellipse 260px 80px at 120px 360px, rgba(240,240,240,.9) 0%, rgba(240,240,240,0) 100%),
    linear-gradient(180deg, rgba(0,0,0,0) 70%, rgba(120,112,100,.55) 88%, var(--city) 100%),
    linear-gradient(180deg, var(--sky) 0%, #93b7d8 35%, var(--haze) 68%, #b7bcbf 100%)}
.booking{left:479px;top:199px;width:339px;height:261px;background:var(--crimson);border-radius:8px;color:var(--white)}
.booking h2{position:absolute;left:0;top:12px;width:100%;text-align:center;font-family:"Marcellus",serif;font-weight:400;font-size:42px}
.rule{position:absolute;left:19px;width:300px;height:2px;background:var(--white)}
.field-label{position:absolute;left:34px;font-size:12.5px}
.field{position:absolute;left:165px;width:137px;height:21px;background:var(--white);color:var(--ink);font-size:12.5px;line-height:21px;padding-left:9px;border:1px solid #ccc}
.field svg{position:absolute;right:6px;top:4px}
.btn-book{position:absolute;left:165px;top:212px;width:83px;height:21px;background:var(--white);color:var(--ink);font-size:12.5px;text-align:center;line-height:21px;border:1px solid #bbb}

/* welcome */
.welcome{left:0;top:524px;width:891px;height:208px;background:var(--mist)}
.welcome h1{position:absolute;left:0;top:19px;width:838px;text-align:center;font-size:26.5px;color:var(--crimson);font-weight:700}
.welcome-car{left:87px;top:66px;width:223px;height:112px;background:radial-gradient(ellipse at center,#b8bcbf 0%,#8e9296 55%,rgba(217,222,220,0) 72%)}
.welcome-text{left:327px;top:57px;width:470px;font-size:13.5px;line-height:16.9px;white-space:nowrap}
.welcome-lead{left:328px;top:143px;font-size:15px;font-style:italic;font-weight:700;color:var(--crimson)}
.read-more{position:absolute;height:17px;background:var(--crimson);color:var(--white);font-size:10.5px;font-weight:700;text-align:center;line-height:17px}

/* content */
.section-title{position:absolute;font-size:20px;font-weight:700;color:var(--crimson)}
.section-text{position:absolute;font-size:12px;font-weight:700;line-height:18.8px;color:var(--ink);white-space:nowrap}
.tile{position:absolute;width:119px;height:27px;color:var(--white);font-size:15px;text-align:center;line-height:27px;background:var(--slate)}
.tile.dark{background:var(--charcoal)}
.city-photo{left:513px;top:760px;width:271px;height:106px;background:linear-gradient(180deg,#7fa6c6 0%,#b9c6cf 55%,#8a8f8c 100%);border:1px solid #999}

/* footer */
.footer{left:0;top:1031px;width:891px;height:96px;background:var(--crimson);color:var(--white)}
.footer-links{position:absolute;left:101px;top:37px;font-size:15px;display:flex;align-items:center}
.footer-links span{padding:0 9px;border-left:1px solid var(--white);color:#f3cfd9}
.footer-links span:first-child{padding-left:0;border-left:none;color:var(--white);font-weight:700}
.call{position:absolute;left:511px;top:28px;font-size:27px}
.copyright{left:101px;top:1136px;font-size:14px}
.social{top:1132px;width:25px;height:25px;border-radius:3px}
</style>
</head>
<body>

<header>
  <div class="abs header"></div>
  <div class="abs nav-band"></div>
  <div class="abs strip"></div>
  <div class="abs brand">
    <div class="brand-mark"></div>
    <div class="brand-name">Crestvane</div>
    <div class="brand-sub">Rent A Car</div>
  </div>
  <div class="abs car-icon" role="img" aria-label="Car silhouette illustration"></div>
  <div class="abs slogan slogan-main">Experience an extra mile</div>
  <div class="abs slogan slogan-sub">of comfort, pleasure &amp; leisure from the best</div>
  <nav class="nav">
    <svg class="abs home-icon" width="14" height="13" viewBox="0 0 14 13" aria-label="Home"><path d="M1 7 L7 1 L13 7 M3 5.5 V12 H11 V5.5 M6 12 V8.5 H8 V12" fill="none" stroke="#e7b6c4" stroke-width="1.5"/></svg>
    <div class="abs nav-sep" style="left:416px"></div>
    <a style="left:441px">About</a>
    <div class="abs nav-sep" style="left:506px"></div>
    <a style="left:523px">Our Team</a>
    <div class="abs nav-sep" style="left:618px"></div>
    <a style="left:638px">Strategy</a>
    <div class="abs nav-sep" style="left:721px"></div>
    <a style="left:738px">Contact</a>
  </nav>
</header>

<section>
  <div class="abs hero" role="img" aria-label="Photo of three happy women in a white convertible in front of the Dubai skyline"></div>
  <form class="abs booking">
    <h2>Book Your Car</h2>
    <div class="rule" style="top:67px"></div>
    <div class="field-label" style="top:85px">Pick-up Location from</div>
    <div class="field" style="top:81px">Dubai Air Port
      <svg width="11" height="9" viewBox="0 0 11 9"><path d="M0 0 H11 L5.5 9Z" fill="#888"/></svg></div>
    <div class="field-label" style="top:125px">Pick-up Date</div>
    <div class="field" style="top:121px">27th Mar. 2015
      <svg width="15" height="13" viewBox="0 0 15 13"><path d="M.5 .5H14.5V12.5H.5ZM.5 4.5H14.5M.5 8.5H14.5M5 .5V12.5M10 .5V12.5" fill="none" stroke="#bbb"/></svg></div>
    <div class="field-label" style="top:164px">Pick-up Time</div>
    <div class="field" style="top:160px">07 : 30 AM
      <svg width="14" height="14" viewBox="0 0 14 14" style="top:3px"><circle cx="7" cy="7" r="7" fill="#999"/><path d="M4 7 L6.5 9 L10 4.5" fill="none" stroke="#fff" stroke-width="1.5"/></svg></div>
    <div class="rule" style="top:197px"></div>
    <div class="btn-book">Book</div>
  </form>
</section>

<section class="abs welcome">
  <h1>Welcome to Crestvane Book your car now</h1>
  <div class="abs welcome-car" role="img" aria-label="Silver sports car"></div>
  <p class="abs welcome-text">As Dubai is expected to welcome millions of tourists and visitors,<br>car rental industry is believed to escalate more rapidly in the region.<br>Over the past five years, demands for car rentals in Dubai has been aug-<br>menting at a healthy pace and is currently registering a growth rate of 20<br>to 25 percent per year.</p>
  <div class="abs welcome-lead">The swift economic growth and.....</div>
  <div class="read-more" style="left:328px;top:170px;width:87px">Read More</div>
</section>

<main>
  <h2 class="section-title" style="left:128px;top:761px">Servicess</h2>
  <p class="section-text" style="left:131px;top:796px">Crestvane offers a comprehensive range of<br>services including daily, short term and long<br>term rental, chauffeur drive services for<br>every purpose and budget.</p>
  <div class="read-more" style="left:308px;top:874px;width:88px">Read More</div>

  <h2 class="section-title" style="left:128px;top:912px">Rates, Terms &amp; Conditions</h2>
  <div class="tile" style="left:129px;top:945px">Rates</div>
  <div class="tile dark" style="left:276px;top:945px">Insurance</div>
  <div class="tile" style="left:129px;top:983px">Documents</div>
  <div class="tile" style="left:276px;top:983px">General</div>

  <div class="abs city-photo" role="img" aria-label="Photo of Dubai skyscrapers"></div>
  <h2 class="section-title" style="left:514px;top:875px;font-size:18px">Mission &amp; Vision</h2>
  <p class="section-text" style="left:514px;top:905px">To be one of the leading auto leasing company in<br>the fast growing economy and tourism industry of<br>the emirate of Dubai and play alongside....</p>
  <div class="read-more" style="left:514px;top:974px;width:87px">Read More</div>
</main>

<footer>
  <div class="abs footer">
    <div class="footer-links"><span>Home</span><span>About</span><span>Our Team</span><span>Strategy</span><span>Contact</span></div>
    <div class="call">Call Us: +971 45550192</div>
  </div>
  <div class="abs copyright">© Copyright 2011, Crestvane. All rights reserved.</div>
  <div class="abs social" style="left:516px;background:#4aa3d8" role="img" aria-label="Social link"></div>
  <div class="abs social" style="left:552px;background:#3b5a98" role="img" aria-label="Social link"></div>
  <div class="abs social" style="left:587px;background:#555" role="img" aria-label="Social link"></div>
  <div class="abs social" style="left:622px;background:#f2a51c" role="img" aria-label="Feed link"></div>
</footer>

</body>
</html>
```